Los Brava Dip – CPG Website with WordPress - Store Locator: WP Maps plugin

Larkfield Food Company is a startup consumer packaged goods (CPG) brand launching its flagship product line — Los Brava Dip. We’re seeking a talented web designer to create a bold, professional, mobile-optimized website using WordPress with a WP Maps store locator to help customers find local retailers.

Our goal is to build a strong online presence that supports both retail growth and direct-to-consumer sales.

See Los Brava _Website_Design_Brief word document.

The website URL is https://losbravadip.example/

Target Market(s)

Consumers of gourmet salsa

Industry/Entity Type

Consumer Packaged Goods - Salsa manufacturer.

Coding

Coded - Design and coding required

Number of Pages Required

5+ page

Requirements
Must have
• The design of the Los Brava Dip website shall emulate the clean, polished aesthetic of Fennigo.example.

```html
<!DOCTYPE html>
<html lang="en">
<head>
<meta charset="utf-8">
<title>Los Brava Dip</title>
<link rel="stylesheet" href="https://fonts.googleapis.com/css2?family=Domine:wght@400;700&family=Roboto:wght@400;500;700&display=swap">
<style>
:root{
  --red:#c8202a;
  --red-dark:#a5161f;
  --green:#3d6b1e;
  --ink:#1b1b1b;
  --text:#444;
  --white:#fff;
  --slate:#2f3033;
}
*{box-sizing:border-box;margin:0;padding:0}
html,body{width:1200px;height:4107px;overflow:hidden}
body{font-family:"Roboto",sans-serif;color:var(--ink);background:var(--white);position:relative}
.abs{position:absolute}
h1,h2,h3,.serif{font-family:"Domine",serif;font-weight:700}
.btn{position:absolute;display:flex;align-items:center;justify-content:center;background:var(--red);color:var(--white);border-radius:24px;font-size:15px;font-weight:500}
.btn.green{background:var(--green)}

/* header */
.site-header{position:absolute;left:0;top:0;width:1200px;height:85px;background:var(--white)}
.brand{position:absolute;font-family:"Domine",serif;font-weight:700;color:var(--red);font-size:30px;display:flex;align-items:center;gap:8px}
.brand .dot{width:14px;height:14px;background:var(--red);border-radius:50%}
.nav{position:absolute;left:457px;top:30px;display:flex;gap:26px;font-size:16px;color:#333}
.nav .active{color:var(--red);text-decoration:underline;text-underline-offset:4px}

/* hero */
.hero{position:absolute;left:0;top:85px;width:1200px;height:585px;background:linear-gradient(120deg,#3a3b3e 0%,#2a2b2d 55%,#3b3d40 100%)}
.hero-photo{position:absolute;left:560px;top:30px;width:620px;height:420px;border-radius:40px;background:radial-gradient(circle at 62% 55%,#d8431f 0%,#a83218 30%,rgba(60,60,62,0) 62%)}
.hero h1{position:absolute;left:112px;top:110px;font-size:54px;line-height:65px;color:var(--white)}
.hero p{position:absolute;left:112px;top:265px;font-size:16px;color:#eee}

/* about */
.about-photo{left:112px;top:741px;width:446px;height:376px;border-radius:14px;background:linear-gradient(135deg,#6d9a2c 0%,#c9451c 45%,#e08a2a 100%)}
.about h2{position:absolute;left:641px;top:722px;font-size:40px}
.accent{color:var(--red)}
.about .copy{position:absolute;left:641px;top:788px;width:446px;font-size:14.5px;line-height:26.5px;color:var(--text);height:266px;overflow:hidden}

/* products */
.products{position:absolute;left:0;top:1203px;width:1200px;height:705px;background:var(--red)}
.products h2{position:absolute;left:0;width:1200px;text-align:center;top:68px;font-size:40px;color:var(--white)}
.card{position:absolute;background:var(--white);border-radius:14px}
.product{top:147px;width:309px;height:454px}
.jar{position:absolute;left:80px;top:22px;width:150px;height:248px;border-radius:30px 30px 24px 24px}
.product .name{position:absolute;width:100%;text-align:center;top:283px;font-size:23px}
.product .price{position:absolute;width:100%;text-align:center;top:322px;font-size:36px}
.product .btn{left:78px;top:383px;width:153px;height:44px}
.sale{position:absolute;right:-2px;top:-2px;width:86px;height:36px;background:var(--green);color:var(--white);border-radius:18px;font-family:"Domine",serif;font-weight:700;font-size:17px;display:flex;align-items:center;justify-content:center}

/* recipes */
.section-title{position:absolute;left:0;width:1200px;text-align:center;font-size:40px}
.recipe{left:112px;top:2069px;width:978px;height:497px;border:2px solid var(--red);border-radius:14px}
.recipe-photo{position:absolute;left:62px;top:10px;width:340px;height:474px;border-radius:12px;background:linear-gradient(160deg,#8c5a36 0%,#c4652a 50%,#9a3e1b 100%)}
.recipe h3{position:absolute;left:485px;top:28px;font-size:27px}
.recipe .copy{position:absolute;left:487px;top:78px;width:455px;font-size:14.5px;line-height:26.5px;color:var(--text);height:186px;overflow:hidden}
.recipe h4{position:absolute;left:484px;top:274px;font-family:"Domine",serif;font-size:27px}
.recipe ul{position:absolute;left:487px;top:316px;list-style:none;font-size:14.5px;line-height:27px;color:var(--text)}
.recipe .btn{left:487px;top:416px;width:153px;height:44px}
.arrow{position:absolute;width:28px;height:28px;border-radius:50%;display:flex;align-items:center;justify-content:center}

/* reviews */
.reviews{position:absolute;left:0;top:2651px;width:1200px;height:526px;background:var(--red)}
.reviews h2{position:absolute;left:0;width:1200px;text-align:center;top:72px;font-size:40px;color:var(--white)}
.review{top:167px;width:309px;height:274px}
.stars{position:absolute;left:28px;top:32px;display:flex;gap:3px}
.review .title{position:absolute;left:28px;top:74px;font-size:16px;font-weight:500}
.review .body{position:absolute;left:28px;top:106px;width:260px;font-size:14.5px;line-height:27px;color:var(--text)}
.avatar{position:absolute;left:28px;top:170px;width:70px;height:70px;border-radius:50%;background:linear-gradient(135deg,#c9b8a6,#6f5d4f)}
.who{position:absolute;left:116px;top:182px;font-size:16px;line-height:25px}

/* social feed */
.feed{top:3338px;width:233px;height:240px;border-radius:12px}
.feed.framed{border:2px solid var(--green)}
.feed-badge{position:absolute;left:20px;top:20px;width:30px;height:30px;border-radius:8px;background:var(--red)}

/* footer */
.footer{position:absolute;left:0;top:3640px;width:1200px;height:467px}
.footer-bg{position:absolute;left:0;top:0}
.foot-col{position:absolute;top:162px;color:var(--white)}
.foot-col h5{font-family:"Domine",serif;font-size:17px;font-weight:700;margin-bottom:18px}
.foot-col ul{list-style:none;font-size:15.5px;line-height:34px}
.foot-col li.sq::before{content:"";display:inline-block;width:8px;height:8px;background:var(--white);margin-right:14px;vertical-align:middle}
.contact li{display:flex;align-items:flex-start;gap:16px;line-height:24px;margin-bottom:12px}
.contact svg{flex:none;margin-top:3px}
.social{position:absolute;left:148px;top:276px;display:flex;gap:14px}
.social span{width:22px;height:22px;border-radius:50%;background:var(--white)}
.rule{position:absolute;left:112px;top:398px;width:978px;height:1px;background:rgba(255,255,255,.35)}
.copyright{position:absolute;left:0;width:1200px;top:415px;text-align:center;color:var(--white);font-size:13px}
</style>
</head>
<body>

<header class="site-header">
  <div class="brand" style="left:108px;top:20px"><span class="dot"></span>Los Brava</div>
  <nav class="nav">
    <span class="active">Home</span><span>Products</span><span>Where to Buy</span><span>Recipes</span><span>About</span><span>Review</span>
  </nav>
  <div class="btn" style="left:969px;top:22px;width:120px;height:42px;">Contact Us</div>
</header>

<section class="hero">
  <div class="hero-photo" role="img" aria-label="Bowl of red salsa with fresh tomatoes, red chili peppers, basil and spices on dark slate"></div>
  <h1>Taste the Boldness of<br>Los Brava.</h1>
  <p>All-natural salsas made in Texas with fire-roasted flavor.</p>
  <div class="btn" style="left:112px;top:321px;width:119px;height:44px;">Get Started</div>
  <svg class="abs" style="left:0;top:455px" width="1200" height="130" viewBox="0 0 1200 130">
    <path d="M0 120 C300 110 520 60 760 40 C900 28 1010 45 1120 65 L1200 80 L1200 130 L0 130 Z" fill="#fff"/>
    <path d="M0 120 C300 110 520 60 760 40 C900 28 1010 45 1120 65 L1200 80" fill="none" stroke="#c8202a" stroke-width="7"/>
  </svg>
</section>

<section class="about">
  <div class="abs about-photo" role="img" aria-label="Clay bowl of salsa with tortilla chips and red chili peppers"></div>
  <h2>About <span class="accent">Los Brava</span></h2>
  <div class="copy">
    <p>Los Brava was founded in 2025 with a simple vision: to create bold, premium salsas that deliver authentic flavor using real, honest ingredients. What began as a homegrown recipe has grown into a professionally scaled brand, built for regional retail distribution and future expansion.</p>
    <p>Crafted in small batches using vine-ripened crushed tomatoes, real chili pepper purees, and carefully balanced natural spices, each Los Brava variety offers rich texture and depth—without fillers, preservatives, or shortcuts. From the classic All Natural to the Habanero, every jar reflects a commitment to quality and care.</p>
  </div>
  <div class="btn" style="left:641px;top:1076px;width:121px;height:42px;">Read More</div>
</section>

<section class="products">
  <h2>Our Products</h2>
  <div class="card product" style="left:112px">
    <div class="jar" role="img" aria-label="Jar of All Natural salsa" style="background:linear-gradient(180deg,#b89a4a 0 14%,#c4361e 14% 100%)"></div>
    <div class="name serif">All Natural</div>
    <div class="price serif">$10</div>
    <div class="btn">Shop Now</div>
  </div>
  <div class="card product" style="left:446px">
    <div class="sale">Sale</div>
    <div class="jar" role="img" aria-label="Jar of Habanero salsa" style="background:linear-gradient(180deg,#b89a4a 0 14%,#b8301c 14% 100%)"></div>
    <div class="name serif" style="color:var(--green)">Habanero</div>
    <div class="price serif" style="color:var(--green)">$10</div>
    <div class="btn green">Add to Cart</div>
  </div>
  <div class="card product" style="left:781px">
    <div class="jar" role="img" aria-label="Jar of Verde salsa" style="background:linear-gradient(180deg,#b89a4a 0 14%,#8ea23a 14% 100%)"></div>
    <div class="name serif">Verde</div>
    <div class="price serif">$10</div>
    <div class="btn">Shop Now</div>
  </div>
</section>

<section>
  <h2 class="section-title" style="top:1978px">Our <span class="accent">Recipes</span></h2>
  <div class="arrow" style="left:43px;top:2297px;background:var(--green)"><svg width="12" height="12" viewBox="0 0 12 12"><path d="M8 1 L3 6 L8 11" fill="none" stroke="#fff" stroke-width="2"/></svg></div>
  <div class="arrow" style="left:1131px;top:2297px;background:#93b07a"><svg width="12" height="12" viewBox="0 0 12 12"><path d="M4 1 L9 6 L4 11" fill="none" stroke="#fff" stroke-width="2"/></svg></div>
  <div class="card recipe abs">
    <div class="recipe-photo" role="img" aria-label="Spoonful of cheesy Mexican beef and rice"></div>
    <h3>One Pot Mexican Beef and Rice</h3>
    <div class="copy">
      <p>This One Pot Mexican Beef and Rice is the ultimate weeknight dinner—quick to prepare, easy to clean up, and packed with bold flavor in every bite. Ground beef is browned and simmered with beef broth, sweet corn, and Los Brava salsa, then combined with instant rice and melted cheddar for a hearty, satisfying meal that comes together in just 30 minutes.</p>
      <p>The star of the dish is Los Brava salsa, which infuses the beef</p>
    </div>
    <h4>Ingredients</h4>
    <ul><li>1 pound ground beef</li><li>2 cups low sodium beef broth</li><li>One 16-ounce jar Los Brava salsa</li></ul>
    <div class="btn">Read More</div>
  </div>
</section>

<section class="reviews">
  <h2>What People Are Saying About Los Brava</h2>
  <div class="arrow" style="left:43px;top:278px;background:var(--white)"><svg width="12" height="12" viewBox="0 0 12 12"><path d="M8 1 L3 6 L8 11" fill="none" stroke="#c8202a" stroke-width="2"/></svg></div>
  <div class="arrow" style="left:1131px;top:278px;background:#e07b80"><svg width="12" height="12" viewBox="0 0 12 12"><path d="M4 1 L9 6 L4 11" fill="none" stroke="#c8202a" stroke-width="2"/></svg></div>

  <div class="card review" style="left:112px">
    <div class="stars"><svg width="105" height="18" viewBox="0 0 105 18"><g fill="#f29a12"><path id="st" d="M9 0 L11.6 6 L18 6.5 L13 10.7 L14.6 17 L9 13.6 L3.4 17 L5 10.7 L0 6.5 L6.4 6 Z"/><use href="#st" x="21"/><use href="#st" x="42"/><use href="#st" x="63"/><use href="#st" x="84"/></g></svg></div>
    <div class="title">Very good, and I’m a salsa</div>
    <div class="body">This one stood out in the blind taste test for its balance and freshness.</div>
    <div class="avatar" role="img" aria-label="Customer portrait"></div>
    <div class="who">Mara<br>Customer</div>
  </div>
  <div class="card review" style="left:446px">
    <div class="stars"><svg width="105" height="18" viewBox="0 0 105 18"><g fill="#f29a12"><use href="#st"/><use href="#st" x="21"/><use href="#st" x="42"/><use href="#st" x="63"/><use href="#st" x="84"/></g></svg></div>
    <div class="title">Awesome taste, fresh.</div>
    <div class="body">Authentic flavor that impressed even picky palates.</div>
    <div class="avatar" role="img" aria-label="Customer portrait"></div>
    <div class="who">Theo<br>Customer</div>
  </div>
  <div class="card review" style="left:781px">
    <div class="stars"><svg width="105" height="18" viewBox="0 0 105 18"><g fill="#f29a12"><use href="#st"/><use href="#st" x="21"/><use href="#st" x="42"/><use href="#st" x="63"/><use href="#st" x="84"/></g></svg></div>
    <div class="title">Really good flavor.</div>
    <div class="body">Simple, clean ingredients that make a real difference.</div>
    <div class="avatar" role="img" aria-label="Customer portrait"></div>
    <div class="who">Priya<br>Customer</div>
  </div>
</section>

<section>
  <h2 class="section-title" style="top:3250px">Follow Los Brava <span class="accent">on Snapfeed</span></h2>
  <div class="abs feed" style="left:112px;background:linear-gradient(150deg,#c9b53a,#7a5a3a)" role="img" aria-label="Woman enjoying chips and salsa at a table"></div>
  <div class="abs feed" style="left:359px;background:linear-gradient(150deg,#9a8a80,#5a3a30)" role="img" aria-label="Two friends sharing chips and salsa"></div>
  <div class="abs feed framed" style="left:607px;background:linear-gradient(150deg,#f1efee,#d8cfc9)" role="img" aria-label="Woman dipping a chip in salsa"><span class="feed-badge"></span></div>
  <div class="abs feed" style="left:856px;background:linear-gradient(150deg,#a89488,#c4452a)" role="img" aria-label="Woman biting a red pepper"></div>
</section>

<footer class="footer">
  <svg class="footer-bg" width="1200" height="467" viewBox="0 0 1200 467">
    <path d="M0 95 C260 130 520 110 760 70 C920 42 1080 25 1200 18 L1200 467 L0 467 Z" fill="#c8202a"/>
    <path d="M0 95 C260 130 520 110 760 70 C920 42 1080 25 1200 18" fill="none" stroke="#3d6b1e" stroke-width="7"/>
  </svg>
  <div class="brand" style="left:112px;top:170px;color:var(--white);font-size:32px"><span class="dot" style="background:var(--white)"></span>Los Brava</div>
  <div class="social"><span></span><span></span><span></span></div>

  <div class="foot-col" style="left:386px">
    <h5>Quick Links</h5>
    <ul><li class="sq">Home</li><li class="sq">Prodcut</li><li class="sq">Where to Buy</li><li class="sq">Receipe</li><li class="sq">About</li><li class="sq">Review</li></ul>
  </div>
  <div class="foot-col" style="left:580px">
    <h5>Help Links</h5>
    <ul><li class="sq">Privacy Policy</li><li class="sq">Shipping Policy</li><li class="sq">Terms and Conditions</li></ul>
  </div>
  <div class="foot-col contact" style="left:827px">
    <h5>Contact Us</h5>
    <ul>
      <li><svg width="18" height="18" viewBox="0 0 18 18"><circle cx="9" cy="9" r="9" fill="#fff"/><path d="M6 4.5 L7.6 6.6 L6.8 7.8 C7.5 9.3 8.7 10.5 10.2 11.2 L11.4 10.4 L13.5 12 L12.6 13.4 C8.6 13.2 4.8 9.4 4.6 5.4 Z" fill="#c8202a"/></svg>+1 555 014 2207</li>
      <li><svg width="18" height="18" viewBox="0 0 18 18"><circle cx="9" cy="9" r="9" fill="#fff"/><rect x="4.5" y="6" width="9" height="6.5" fill="none" stroke="#c8202a" stroke-width="1.4"/><path d="M4.5 6 L9 9.5 L13.5 6" fill="none" stroke="#c8202a" stroke-width="1.4"/></svg>info@losbravadip.example</li>
      <li><svg width="18" height="18" viewBox="0 0 18 18"><circle cx="9" cy="9" r="9" fill="#fff"/><path d="M9 3.5 C6.6 3.5 5 5.2 5 7.3 C5 10 9 14.5 9 14.5 C9 14.5 13 10 13 7.3 C13 5.2 11.4 3.5 9 3.5 Z" fill="#c8202a"/><circle cx="9" cy="7.3" r="1.5" fill="#fff"/></svg>220 Alder Row, Suite 4,<br>Austin, TX 78701,</li>
    </ul>
  </div>
  <div class="rule"></div>
  <div class="copyright">Copyright © 2025 Los Brava Dip - All Rights Reserved.</div>
</footer>

</body>
</html>
```